Unique Business Card Design

Unique Business Card design for our orthotic and prosthetic company. Our logo is on our website, color is light blue. Unique shape (artificial leg shaped, vertical, etc..) preferred. Logo, business name, individual name and basic demographics needed.

Industry/Entity Type

Business

Contact Information for Business Card

Logo, Industry, Phone # Logo, "Prosthetic & Orthotic Services" Place to add individual name and contact info

Colors
cee9f5

Requirements
Must have
• The icon must be there, placement of "Prosthetic & Orthotic Services" can be moved
Nice to have
• Like the mix of light blue, and a little darker blue. One design included the icons from my website which was a nice touch

```html
<!DOCTYPE html>
<html lang="en">
<head>
<meta charset="utf-8">
<title>Limbwell Inc. Business Card</title>
<link href="https://fonts.googleapis.com/css2?family=Open+Sans:wght@400;600;700&family=Roboto:wght@400;500;700&family=Cormorant+Garamond:ital,wght@1,500&display=swap" rel="stylesheet">
<style>
  :root {
    --bg: #d6d8db;
    --blue-deep: #0a58ad;
    --blue-mid: #1a8fdc;
    --blue-bright: #22a0e8;
    --blue-text: #1658a8;
    --sky: #cee9f5;
    --ink: #2b2b2b;
    --white: #ffffff;
    --rule: #d5d5d5;
  }
  * { box-sizing: border-box; margin: 0; padding: 0; }
  html, body { width: 1200px; height: 1000px; overflow: hidden; }
  body { background: var(--bg); position: relative; font-family: "Roboto", sans-serif; }

  .card {
    position: absolute; left: 220px; width: 760px; border-radius: 28px; overflow: hidden;
    box-shadow: 0 6px 18px rgba(0,0,0,0.25);
  }
  .card--front {
    top: 50px; height: 434px;
    background: linear-gradient(90deg, var(--blue-deep) 0%, var(--blue-mid) 28%, var(--blue-bright) 50%, var(--blue-mid) 72%, var(--blue-deep) 100%);
  }
  .card--back { top: 523px; height: 437px; background: var(--white); }

  .brand { position: absolute; display: flex; align-items: center; }
  .brand__dot { border-radius: 50%; flex: none; }
  .brand__name { font-family: "Open Sans", sans-serif; font-weight: 600; line-height: 1; letter-spacing: 0.2px; }
  .brand__tagline { font-family: "Cormorant Garamond", serif; font-style: italic; font-weight: 500; }

  .card--front .brand { left: 138px; top: 111px; }
  .card--front .brand__dot { width: 132px; height: 132px; background: var(--white); margin-right: 16px; }
  .card--front .brand__name { color: var(--white); font-size: 40px; }
  .card--front .brand__rule { height: 4px; background: var(--white); margin: 6px 0 8px; width: 332px; }
  .card--front .brand__tagline { color: var(--white); font-size: 24px; padding-left: 22px; }

  .services { position: absolute; top: 309px; left: 0; width: 100%; }
  .service { position: absolute; width: 120px; text-align: center; color: var(--white); font-size: 15px; font-family: "Open Sans", sans-serif; }
  .service__icon {
    display: block; width: 58px; height: 58px; margin: 0 auto 10px; border-radius: 50%;
    background: radial-gradient(circle at 40% 35%, #f2f8ff 0%, var(--sky) 55%, #8fc2ee 100%);
    border: 2px solid rgba(255,255,255,0.8);
  }

  .card--back .brand { left: 44px; top: 44px; }
  .card--back .brand__dot { width: 84px; height: 84px; background: var(--blue-deep); margin-right: 10px; }
  .card--back .brand__name { color: var(--blue-text); font-size: 24px; }
  .card--back .brand__rule { height: 3px; background: var(--blue-text); margin: 4px 0 6px; width: 216px; }
  .card--back .brand__tagline { color: var(--blue-text); font-size: 16px; padding-left: 14px; }

  .person { position: absolute; left: 137px; top: 146px; width: 190px; }
  .person__name { color: var(--blue-text); font-weight: 700; font-size: 22px; }
  .person__title { color: var(--ink); font-size: 16px; margin-top: 2px; padding-bottom: 10px; border-bottom: 1px solid var(--rule); }

  .address { position: absolute; left: 137px; top: 218px; color: var(--ink); font-size: 17px; line-height: 22px; }

  .contacts { position: absolute; left: 137px; top: 276px; list-style: none; color: var(--ink); font-size: 17px; }
  .contacts li { display: flex; align-items: center; height: 24.4px; }
  .contacts svg { width: 13px; height: 13px; margin-right: 6px; fill: var(--blue-text); flex: none; }
  .contacts .accent { color: var(--blue-text); }

  .back-panel { position: absolute; right: 0; top: 0; width: 344px; height: 437px; }
</style>
</head>
<body>

<section class="card card--front">
  <div class="brand">
    <span class="brand__dot"></span>
    <div>
      <div class="brand__name">LIMBWELL INC.</div>
      <div class="brand__rule"></div>
      <div class="brand__tagline">Prosthetic &amp; Orthotic Services</div>
    </div>
  </div>
  <div class="services">
    <div class="service" style="left:192px"><span class="service__icon" role="img" aria-label="Orthotics icon: knee joint"></span>Orthotics</div>
    <div class="service" style="left:325px"><span class="service__icon" role="img" aria-label="Prosthetics icon: standing child"></span>Prosthetics</div>
    <div class="service" style="left:449px"><span class="service__icon" role="img" aria-label="Vascular icon: wheelchair"></span>Vascular</div>
  </div>
</section>

<section class="card card--back">
  <div class="brand">
    <span class="brand__dot"></span>
    <div>
      <div class="brand__name">LIMBWELL INC.</div>
      <div class="brand__rule"></div>
      <div class="brand__tagline">Prosthetic &amp; Orthotic Services</div>
    </div>
  </div>

  <div class="person">
    <div class="person__name">Miriam Kestler</div>
    <div class="person__title">CO LPO</div>
  </div>

  <div class="address">2380 West 14th Avenue<br>Brooklyn, NY 11214</div>

  <ul class="contacts">
    <li><svg viewBox="0 0 12 12"><path d="M3 0h6a1 1 0 0 1 1 1v10a1 1 0 0 1-1 1H3a1 1 0 0 1-1-1V1a1 1 0 0 1 1-1zm0 2v7h6V2z"/></svg>845-5550192</li>
    <li><svg viewBox="0 0 12 12"><path d="M2 1l2.5-.5 1.2 3-1.5 1a6 6 0 0 0 3.3 3.3l1-1.5 3 1.2L11 10c-5 1-10-4-9-9z"/></svg>(718) 555-0140</li>
    <li><svg viewBox="0 0 12 12"><path d="M3 0h6v3H3zM1 4h10v5H9v3H3V9H1zm3 4v3h4V8z"/></svg>(718) 555-0163</li>
    <li><svg viewBox="0 0 12 12"><path d="M0 2h12v1L6 7 0 3zm0 2.2l6 4 6-4V10H0z"/></svg>mkestler@limbwellinc.com</li>
    <li><svg viewBox="0 0 12 12"><path d="M6 0a6 6 0 1 0 0 12A6 6 0 0 0 6 0zm0 1c.8.8 1.4 2.3 1.5 4.5h-3C4.6 3.3 5.2 1.8 6 1zM1 5.5a5 5 0 0 1 2.6-3.9C3 2.7 2.6 4 2.5 5.5zm0 1h1.5c.1 1.5.5 2.8 1.1 3.9A5 5 0 0 1 1 6.5zm3.5 0h3c-.1 2.2-.7 3.7-1.5 4.5-.8-.8-1.4-2.3-1.5-4.5zm4 0H11a5 5 0 0 1-2.6 3.9c.6-1.1 1-2.4 1.1-3.9zm0-1c-.1-1.5-.5-2.8-1.1-3.9A5 5 0 0 1 11 5.5z"/></svg>www.<span class="accent">limbwellinc</span>.net</li>
  </ul>

  <svg class="back-panel" viewBox="0 0 344 437" role="img" aria-label="Large blue decorative panel where the company emblem of a standing figure appears">
    <defs>
      <linearGradient id="panelFill" x1="0" y1="0" x2="1" y2="0">
        <stop offset="0" stop-color="#0a58ad"/>
        <stop offset="0.55" stop-color="#1a8fdc"/>
        <stop offset="1" stop-color="#3aa8ea"/>
      </linearGradient>
    </defs>
    <circle cx="280" cy="217" r="264" fill="url(#panelFill)"/>
  </svg>
</section>

</body>
</html>
```